Granite Tile Retail Website

We need wireframe PSD for a website selling granite tile. There are 4 custom pages, shopping cart page, and checkout page. I have a logo designed but the color scheme is up to you.
Color Gallery - We have approximately 20 different stone colors. Each color will have a little gallery of its own pictures. On this page the customer can also add a sample piece of the color they are viewing to their shopping cart.
Questions Page - This page has 3 elements
1. Upload or fax diagram of kitchen for quotation
2. Installation video
3. Installation FAQ (text)
Order Page - This page has 3 steps for the customer
1. Customer chooses his color.
2. For each color we have numerous different products. He inputs the quantity of each product.
3. Customer is given total price and shipping quote. If order over $500 it says "This order qualifies for free shipping". Customer can click on button to "Order Now"
Shopping Cart - Very standard, just like I have attached here. Just modify for your colors / font.
Checkout - Just like in the attached. See design-explanation.docx for minor adjustments.
I have vector file for logo.
Updates
Please try to post your designs by tonightÂ
Target Market(s)
Home owners 40-60 years old
Industry/Entity Type
Shopping
Look and feel

```html
<!DOCTYPE html>
<html lang="en">
<head>
<meta charset="utf-8">
<title>Stonevale Granite — Colors Gallery</title>
<link href="https://fonts.googleapis.com/css2?family=Oswald:wght@400;500&family=Open+Sans:wght@400&display=swap" rel="stylesheet">
<style>
:root{
  --bg:#ececec;
  --page:#ffffff;
  --band:#f3f3f3;
  --line:#dcdcdc;
  --ink:#4a4a4a;
  --ink-dark:#333333;
  --gold:#e2a940;
  --maroon:#4a1a2a;
  --panel:rgba(34,30,30,.82);
  --panel-ink:#ffffff;
}
*{margin:0;padding:0;box-sizing:border-box}
html,body{width:946px;height:1200px;overflow:hidden}
body{background:var(--bg);font-family:"Oswald",sans-serif;color:var(--ink);position:relative}
.page{position:absolute;left:35px;top:35px;width:876px;height:1123px;background:var(--page);border:1px solid #e2e2e2}
.header{position:absolute;left:53px;top:57px;width:840px;height:103px;background:linear-gradient(#fafafa,#efefef);border-top:1px solid var(--line);border-bottom:1px solid var(--line)}
.brand{position:absolute;left:26px;top:30px;display:flex;align-items:center;gap:10px}
.brand-mark{width:26px;height:26px;background:var(--maroon)}
.brand-name{font-weight:500;font-size:24px;color:var(--maroon);letter-spacing:1px}
.nav{position:absolute;right:26px;top:26px;display:flex;height:52px;align-items:center}
.nav a{font-size:19px;color:#555;text-decoration:none;padding:0 10px;line-height:52px;border-left:1px solid #bbb}
.nav a:first-child{border-left:none}
.nav a.active{color:var(--gold)}
.section-title{position:absolute;left:62px;top:190px;font-size:23px;font-weight:400;color:var(--ink-dark)}
.swatches{position:absolute;left:70px;top:227px;display:grid;grid-template-columns:110px 110px;column-gap:18px;row-gap:0}
.swatch{height:88px}
.swatch-label{display:block;font-size:12px;line-height:16px;color:var(--ink-dark)}
.swatch-chip{display:block;height:70px;border:2px solid rgba(0,0,0,.22)}
.divider{position:absolute;left:341px;top:241px;width:1px;height:775px;background:var(--line)}
.color-title{position:absolute;left:350px;top:236px;font-size:23px;color:var(--ink-dark)}
.color-title small{font-size:17px}
.hero{position:absolute;left:350px;top:265px;width:543px;height:372px;border:3px solid var(--maroon);overflow:hidden}
.hero-photo{position:absolute;inset:0;background:linear-gradient(160deg,#c7d3d0 0%,#aebab5 35%,#a2673a 60%,#7a4a2c 80%,#2c2f30 100%)}
.hero-panel{position:absolute;right:0;top:0;width:172px;height:100%;background:var(--panel);padding:44px 12px 0 14px;color:var(--panel-ink)}
.hero-heading{font-size:19px;line-height:25px;font-weight:500;text-transform:uppercase}
.hero-body{margin-top:22px;font-family:"Open Sans",sans-serif;font-size:11.5px;line-height:14.7px;text-indent:30px}
.sample-btn{position:absolute;left:14px;top:328px;width:146px;height:30px;background:var(--gold);display:flex;align-items:center;gap:8px;padding-left:10px;color:var(--maroon);font-size:13.5px;font-weight:500;text-decoration:none}
.thumbs{position:absolute;left:350px;top:656px;display:grid;grid-template-columns:repeat(4,130px);column-gap:7px;row-gap:7px}
.thumb{height:84px;border:1px solid #999}
.thumb.a{background:linear-gradient(135deg,#8e8a7e,#5b4f3c 55%,#2c2a25)}
.thumb.b{background:linear-gradient(180deg,#f0ece6,#7a2c18 45%,#1d1b1b)}
.thumb.c{background:linear-gradient(180deg,#6a3a16,#c27a2a 50%,#3a2410)}
.footer{position:absolute;left:53px;top:1045px;width:840px;height:103px;background:linear-gradient(#f2f2f2,#fafafa);border-top:1px solid var(--line)}
.footer ul{position:absolute;top:18px;list-style:none}
.footer li{font-size:12.5px;line-height:16.8px;color:var(--ink-dark)}
.footer li.active{color:var(--gold)}
.trust{position:absolute;left:642px;top:20px;display:flex;gap:10px;align-items:flex-start}
.seal{width:62px;height:62px;border-radius:50%;background:#d9c56a}
.badge{width:102px;height:38px;background:#1e5a8c;border-radius:3px}
.badge-bar{width:102px;height:30px;margin-top:6px;background:#2a5fa0;border-radius:3px}
</style>
</head>
<body>
<div class="page"></div>

<header class="header">
  <div class="brand"><span class="brand-mark"></span><span class="brand-name">STONEVALE GRANITE</span></div>
  <nav class="nav">
    <a href="#">HOME</a><a href="#" class="active">GALLERY</a><a href="#">QUESTIONS</a><a href="#">ORDER</a><a href="#">SHOPPING CART</a>
  </nav>
</header>

<h1 class="section-title">COLORS GALLERY</h1>

<div class="swatches">
  <div class="swatch"><span class="swatch-label">01. GIALLO</span><span class="swatch-chip" style="background:#a87c58"></span></div>
  <div class="swatch"><span class="swatch-label">02. TAR BROWN</span><span class="swatch-chip" style="background:#dcb99c"></span></div>
  <div class="swatch"><span class="swatch-label">03. MERT BROWN</span><span class="swatch-chip" style="background:#f1e2d2"></span></div>
  <div class="swatch"><span class="swatch-label">04. VBA TUBA</span><span class="swatch-chip" style="background:#5a2e1a"></span></div>
  <div class="swatch"><span class="swatch-label">05. GIALLO</span><span class="swatch-chip" style="background:#3a3a2a"></span></div>
  <div class="swatch"><span class="swatch-label">06. TAR BROWN</span><span class="swatch-chip" style="background:#4e1428"></span></div>
  <div class="swatch"><span class="swatch-label">07. MERT BROWN</span><span class="swatch-chip" style="background:#2a2d33"></span></div>
  <div class="swatch"><span class="swatch-label">08. VBA TUBA</span><span class="swatch-chip" style="background:#7c8496"></span></div>
  <div class="swatch"><span class="swatch-label">09. GIALLO</span><span class="swatch-chip" style="background:#7a6456"></span></div>
  <div class="swatch"><span class="swatch-label">10. TAR BROWN</span><span class="swatch-chip" style="background:#7d8f4c"></span></div>
  <div class="swatch"><span class="swatch-label">11. MERT BROWN</span><span class="swatch-chip" style="background:#a7837c"></span></div>
  <div class="swatch"><span class="swatch-label">12. VBA TUBA</span><span class="swatch-chip" style="background:#4a524a"></span></div>
  <div class="swatch"><span class="swatch-label">13. GIALLO</span><span class="swatch-chip" style="background:#333333"></span></div>
  <div class="swatch"><span class="swatch-label">14. TAR BROWN</span><span class="swatch-chip" style="background:#4a4444"></span></div>
  <div class="swatch"><span class="swatch-label">15. MERT BROWN</span><span class="swatch-chip" style="background:#48534f"></span></div>
  <div class="swatch"><span class="swatch-label">16. VBA TUBA</span><span class="swatch-chip" style="background:#393939"></span></div>
  <div class="swatch"><span class="swatch-label">17. VBA TUBA</span><span class="swatch-chip" style="background:#7a1630"></span></div>
</div>

<div class="divider"></div>

<h2 class="color-title"><small>06.</small> TAR BROWN</h2>

<section class="hero">
  <div class="hero-photo" role="img" aria-label="Kitchen with wood cabinets and dark granite countertop"></div>
  <div class="hero-panel">
    <p class="hero-heading">Some text goes here - the main idea of the chosen granite</p>
    <p class="hero-body">Donec quam felis, ultricies nec, pellentesque eu, pretium quis, sem. Nulla consequat massa quis enim, fringilla vel, aliquet nlojec, vulputate eget, argtcu. Vitae, justo.</p>
    <a href="#" class="sample-btn">
      <svg width="20" height="16" viewBox="0 0 20 16"><path d="M1 2h3l2 8h10l2-6H5" fill="none" stroke="#4a1a2a" stroke-width="2"/><circle cx="8" cy="13.5" r="1.6" fill="#4a1a2a"/><circle cx="15" cy="13.5" r="1.6" fill="#4a1a2a"/></svg>
      ORDER A SAMPLE »
    </a>
  </div>
</section>

<div class="thumbs">
  <div class="thumb a" role="img" aria-label="Granite countertop with sink"></div>
  <div class="thumb b" role="img" aria-label="Kitchen with red cabinets and black counter"></div>
  <div class="thumb c" role="img" aria-label="Warm lit kitchen with wood cabinets"></div>
  <div class="thumb b" role="img" aria-label="Kitchen with red cabinets and black counter"></div>
  <div class="thumb b" role="img" aria-label="Kitchen with red cabinets and black counter"></div>
  <div class="thumb c" role="img" aria-label="Warm lit kitchen with wood cabinets"></div>
  <div class="thumb a" role="img" aria-label="Granite countertop with sink"></div>
  <div class="thumb c" role="img" aria-label="Warm lit kitchen with wood cabinets"></div>
  <div class="thumb a" role="img" aria-label="Granite countertop with sink"></div>
  <div class="thumb b" role="img" aria-label="Kitchen with red cabinets and black counter"></div>
  <div class="thumb c" role="img" aria-label="Warm lit kitchen with wood cabinets"></div>
</div>

<footer class="footer">
  <ul style="left:27px"><li>HOME</li><li class="active">GALLERY</li><li>QUESTIONS</li><li>ORDER</li><li>SHOPPING CART</li></ul>
  <ul style="left:213px"><li>RETURN POLICY</li><li>SHIPPING POLICY</li><li>PRIVACY</li><li>TERMS OF USE</li><li>CUSTOMER SERVICE</li></ul>
  <ul style="left:420px"><li>NEW LINK</li><li>ANOTHER LINK</li><li>THIRD LINK</li><li>FOURTH LINK</li><li>FIFTH LINK</li></ul>
  <div class="trust">
    <div class="seal"></div>
    <div><div class="badge"></div><div class="badge-bar"></div></div>
  </div>
</footer>
</body>
</html>
```